International professional tennis coach needs a book cover design

This is my 2nd published book, the first one was a #1 on the best seller. I'm looking for a world class book cover design for this new book. The name of my first book was 5 Baseline Habits to Unlock Your Flow Rhythm, located on Bookvale.com

The title of the new book:

Title: The Craft of Rally Mastery
Subtitle: Developing a Strategic Advantage through Competitive Intelligence

I'm uploading our new CRAFT OF RALLY logo that I'd like for you to use as the centerpiece of the book design along with a 21st century design feel that incorporates what the book topic is below::

--> This book is about building competitive intelligence by using tennis data analytics to develop and expand a player's strategic advantage for match play. <--

The colors we would like to use are Blue, Yellow, and Green. These shades of these colors should be bold! (You will see the bold color examples of blues, yellows, and greens that I'm talking about in the logos that are attached here, especially the colors for my Racket GridDrill App logo.

I will upload the Racket GridDrill logo which should go somewhere on the back cover design (small size maybe in the bottom corner).

This book is revolutionary to the standard way of teaching tennis, it is based on a decade of recording and gathering tennis data analytics and then we created on-court practice games to develop better decision making in players for the competitive edge.

My websites are www.elevatedrillzone.com and www.craftofrallymastery.com

```html
<!DOCTYPE html>
<html lang="en">
<head>
<meta charset="utf-8">
<title>The Craft of Rally Mastery – Book Cover</title>
<link href="https://fonts.googleapis.com/css2?family=Lora:wght@400;500&family=Playfair+Display:wght@400;700&display=swap" rel="stylesheet">
<style>
  :root {
    --green: #177512;
    --band-green: #15700f;
    --blue: #0a72c4;
    --ink: #1a1a1a;
    --spine-grey: #555b5f;
    --subtitle: #333333;
    --paper: #ffffff;
    --backdrop: #e5e5e5;
    --rule: #8cc84b;
  }
  * { box-sizing: border-box; margin: 0; padding: 0; }
  html, body { width: 1200px; height: 800px; overflow: hidden; }
  body { background: var(--backdrop); position: relative; font-family: "Lora", Georgia, serif; }

  .cover {
    position: absolute; left: 37px; top: 11px;
    width: 1125px; height: 778px;
    background: var(--paper);
    overflow: hidden;
  }
  .panel { position: absolute; top: 0; height: 100%; }
  .back-cover { left: 0; width: 519px; }
  .spine { left: 519px; width: 87px; border-left: 1px solid #f0f0f0; border-right: 1px solid #f0f0f0; }
  .front-cover { left: 606px; width: 519px; }

  .author-band {
    position: absolute; left: 0; right: 0; top: 718px; height: 60px;
    background: var(--band-green);
  }
  .band-seam { position: absolute; top: 0; bottom: 0; width: 1px; background: rgba(255,255,255,0.14); }

  /* Title: plain set type, one colour, one weight */
  .book-title {
    position: absolute; text-align: center;
    font-family: "Playfair Display", Georgia, serif; font-weight: 700;
    color: var(--green); white-space: nowrap;
  }
  .back-cover .book-title { left: 70px; top: 38px; width: 185px; font-size: 29px; line-height: 34px; }
  .front-cover .book-title { left: 20px; top: 44px; width: 479px; font-size: 70px; line-height: 80px; }

  .brand-name {
    position: absolute; display: flex; align-items: center; justify-content: center; gap: 8px;
    font-family: "Playfair Display", Georgia, serif; font-weight: 700; color: var(--blue);
    white-space: nowrap;
  }
  .brand-name .dot { border-radius: 50%; background: var(--blue); flex: none; }

  /* Back cover */
  .blurb {
    position: absolute; left: 41px; top: 163px; width: 437px;
    font-size: 8.3px; line-height: 11.5px; color: var(--ink); text-align: justify;
  }
  .blurb p + p { margin-top: 2.5px; }
  .blurb .lead { text-align: left; }

  .divider {
    position: absolute; height: 1px;
    background: linear-gradient(90deg, rgba(140,200,75,0), var(--rule) 50%, rgba(140,200,75,0));
  }

  .author-name {
    position: absolute; transform: translateX(-50%);
    font-family: "Playfair Display", Georgia, serif; font-weight: 700;
    font-size: 27px; line-height: 1; color: var(--green); white-space: nowrap;
  }
  .author-photo { position: absolute; left: 41px; width: 101px; }
  .author-photo.coach { top: 391px; height: 107px; background: linear-gradient(160deg, #7a7f82, #3a3d40 55%, #26282b); border-left: 2px solid #3d6fd0; }
  .author-photo.writer { top: 544px; height: 96px; background: linear-gradient(180deg, #8fa9bd, #6f7f70 55%, #2d3440); }
  .author-bio {
    position: absolute; left: 155px; width: 323px;
    font-size: 8.1px; line-height: 11.4px; color: var(--ink); text-align: justify;
  }

  .app-mark {
    position: absolute; left: 52px; top: 652px; width: 76px;
    display: flex; flex-direction: column; align-items: center; gap: 4px;
    font-family: "Lora", Georgia, serif; font-weight: 500; font-size: 7.5px; line-height: 1.05;
    color: var(--blue); text-align: center;
  }
  .app-mark .dot { width: 24px; height: 24px; border-radius: 50%; background: var(--blue); }

  .barcode-box {
    position: absolute; left: 325px; top: 648px; width: 153px; height: 91px;
    background: var(--paper); border: 1px solid #d6d6d6;
  }

  /* Spine */
  .spine-title, .spine-authors {
    position: absolute; left: 0; width: 87px;
    writing-mode: vertical-rl; display: flex; align-items: center; justify-content: flex-start;
    font-family: "Playfair Display", Georgia, serif; font-weight: 700; white-space: nowrap;
  }
  .spine-title { top: 40px; height: 336px; font-size: 24px; color: var(--green); }
  .spine-authors { top: 445px; height: 255px; font-size: 16px; color: var(--spine-grey); letter-spacing: 0.3px; }

  /* Front cover */
  .subtitle {
    position: absolute; left: 0; width: 519px; top: 579px; text-align: center;
    font-family: "Playfair Display", Georgia, serif; font-weight: 400;
    font-size: 22.5px; line-height: 31.5px; letter-spacing: 1.3px; color: var(--subtitle);
  }
  .band-authors {
    position: absolute; left: 606px; width: 519px; top: 728px; text-align: center;
    font-family: "Playfair Display", Georgia, serif; font-weight: 700;
    font-size: 27px; line-height: 40px; color: #fff; letter-spacing: 0.5px;
  }
</style>
</head>
<body>
<main class="cover">

  <div class="author-band">
    <span class="band-seam" style="left:519px"></span>
    <span class="band-seam" style="left:606px"></span>
  </div>

  <!-- Back cover -->
  <section class="panel back-cover">
    <h2 class="book-title">The Craft of<br>Rally<br>Mastery</h2>
    <div class="brand-name" style="left:262px;top:80px;width:172px;font-size:16px;">
      <span class="dot" style="width:12px;height:12px"></span>CRAFT OF RALLY
    </div>

    <div class="blurb">
      <p class="lead">A practical guide on how to win more matches by becoming a more efficient and effective competitor.</p>
      <p>As a tennis player you have the ability to play better matches and win more of them. The Craft of Rally Mastery gives you a system to improve. We start with the individual game of the set itself. Our system examines your physical and mental progression, enabling you to upgrade your movement and performance from shot to shot and point to point. Our system seamlessly integrates the technical (physical) aspects with the tactical (mental/emotional) components, providing a comprehensive approach to elevate this performance. We aim to give you much more than how to hit great shots. Irrespective of your current skill level, we will provide you with a detailed strategic and tactical plan to enhance your performance, leading to improved results and increased success in your matches.</p>
      <p>The Craft of Rally Mastery emphasizes the importance of shifting focus from oneself to the opponent, encouraging players to analyze and understand their adversaries. By bringing the opponent back to the forefront of their thinking, the player creates the best possible context in which to improve as a competitor. In this book, we present a groundbreaking approach to tennis data analytics that seamlessly integrates match performance with practice sessions, and vice versa.</p>
    </div>

    <div class="divider" style="left:105px;width:291px;top:342px"></div>
    <h3 class="author-name" style="left:251px;top:354px">Corwin Ashdale</h3>
    <div class="author-photo coach" role="img" aria-label="Portrait photo of Corwin Ashdale in a white cap on court"></div>
    <p class="author-bio" style="top:394px">Corwin Ashdale is regarded as one of the leading strategy and tactical coaches in the world today. He is the Creator of Racket GridDrill, the world’s first Tennis Tracking App that maps and charts match play based on the rally length of a point. Corwin is a Best Selling Author of the book “5 Baseline Habits to Unlock Your Flow Rhythm” and the Co-Founder of The Craft of Rally Mastery promoting coach, player, and parent development. He is often sought after by coaches around the world to design the practice court in a way that revolutionizes a player’s mindset to successfully negotiate the pressures of competitive match play.</p>

    <div class="divider" style="left:105px;width:291px;top:510px"></div>
    <h3 class="author-name" style="left:246px;top:519px">Reid Talmont</h3>
    <div class="author-photo writer" role="img" aria-label="Portrait photo of Reid Talmont outdoors by a tennis court"></div>
    <p class="author-bio" style="top:557px">Reid Talmont is a writer and tennis coach. He is a Co-Founder at The Craft of Rally Mastery and has been working to create a theoretical framework for tennis players of all levels to improve. Reid studies the forces that act on the player during a tennis match (both internal and external) and works with players to meet the challenge these forces represent. He runs online and on court programs designed specifically to improve a player’s Competitive Intelligence.</p>

    <div class="app-mark"><span class="dot"></span>Racket GridDrill</div>
    <div class="barcode-box"></div>
  </section>

  <!-- Spine -->
  <section class="panel spine">
    <div class="spine-title">The Craft of Rally Mastery</div>
    <div class="brand-name" style="left:0;top:410px;width:87px;font-size:9px;gap:4px;">
      <span class="dot" style="width:7px;height:7px"></span>CRAFT OF RALLY
    </div>
    <div class="spine-authors">Corwin Ashdale &amp; Reid Talmont</div>
  </section>

  <!-- Front cover -->
  <section class="panel front-cover">
    <h1 class="book-title">The Craft of<br>Rally<br>Mastery</h1>

    <div class="brand-name" style="left:35px;top:400px;width:449px;font-size:40px;gap:14px;">
      <span class="dot" style="width:30px;height:30px"></span>CRAFT OF RALLY
    </div>

    <div class="divider" style="left:97px;width:301px;top:570px"></div>
    <p class="subtitle">Developing a Strategic Advantage<br>through Competitive Intelligence</p>
    <div class="divider" style="left:97px;width:301px;top:647px"></div>
  </section>

  <p class="band-authors">Corwin Ashdale &amp; Reid Talmont</p>
</main>
</body>
</html>
```